Business Card Design for company

We want new business cards. We'd like something different-- yet still highly professional. Our tagline is Providing leadership, delivering success. Stock photos are ok, as long as they are relevant and look upscale.

Target Market(s)

Architecture/Business Management Consulting/Engineering Consulting

Contact Information for Business Card

dark gray background with pops of blue might be good, but you tell me. You're the designers. Rounded corners might be nice, but again, you tell me.

Font styles to use
Serif
Sans Serif

Colors
3276b5
5c5c5c
9d9d9d
fbfbfb

Requirements
Nice to have
• Something different, but still very professional.

```html
<!DOCTYPE html>
<html lang="en">
<head>
<meta charset="utf-8">
<title>Halden Group – Business Cards</title>
<link rel="stylesheet" href="https://fonts.googleapis.com/css2?family=Montserrat:wght@600&family=Open+Sans:wght@400;600&display=swap">
<style>
  :root {
    --page-bg: #d9dadc;
    --brand-blue: #3270b0;
    --brand-gray: #4a4b4d;
    --card-white: #f1f1f1;
    --ink-dark: #111111;
    --ink-light: #ffffff;
  }
  * { box-sizing: border-box; margin: 0; padding: 0; }
  html, body { width: 1200px; height: 923px; overflow: hidden; }
  body {
    background: var(--page-bg);
    font-family: "Open Sans", sans-serif;
    display: flex;
    flex-direction: column;
    align-items: center;
    justify-content: center;
    gap: 40px;
  }
  .card {
    position: relative;
    width: 700px;
    height: 400px;
    overflow: hidden;
    box-shadow: 0 6px 18px rgba(0,0,0,0.18);
  }
  .card-shapes { position: absolute; inset: 0; width: 100%; height: 100%; }
  .wordmark {
    position: absolute;
    display: flex;
    align-items: center;
    gap: 14px;
    font-family: "Montserrat", sans-serif;
    font-weight: 600;
    color: var(--brand-gray);
    letter-spacing: 2px;
    text-transform: uppercase;
  }
  .wordmark-square { width: 26px; height: 26px; background: var(--brand-blue); }
  .card-back .wordmark { left: 50%; top: 58px; transform: translateX(-50%); font-size: 40px; }
  .card-front .wordmark { left: 44px; top: 92px; font-size: 36px; }
  .holder { position: absolute; left: 60px; top: 268px; }
  .holder-name { font-size: 24px; font-weight: 600; color: var(--ink-dark); }
  .holder-role { font-size: 15px; color: #333; margin-top: 2px; }
  .contact-list {
    position: absolute;
    right: 28px;
    top: 150px;
    list-style: none;
    color: var(--ink-light);
    font-size: 15px;
    text-align: right;
  }
  .contact-item {
    display: flex;
    align-items: center;
    justify-content: flex-end;
    gap: 10px;
    height: 25px;
  }
  .contact-icon {
    width: 17px; height: 17px;
    background: var(--ink-light);
    border-radius: 3px;
    display: flex; align-items: center; justify-content: center;
    flex-shrink: 0;
  }
  .contact-icon svg { width: 11px; height: 11px; fill: var(--brand-blue); }
</style>
</head>
<body>

  <section class="card card-back" aria-label="Card back">
    <svg class="card-shapes" viewBox="0 0 700 400" preserveAspectRatio="none" aria-hidden="true">
      <rect width="700" height="400" fill="var(--brand-blue)"/>
      <path d="M0 0 H700 V300 C500 300 260 280 0 200 Z" fill="var(--brand-gray)"/>
      <path d="M0 0 H700 V240 C520 250 290 240 0 150 Z" fill="var(--card-white)"/>
    </svg>
    <div class="wordmark"><span class="wordmark-square"></span>Halden Group</div>
  </section>

  <section class="card card-front" aria-label="Card front">
    <svg class="card-shapes" viewBox="0 0 700 400" preserveAspectRatio="none" aria-hidden="true">
      <rect width="700" height="400" fill="var(--brand-gray)"/>
      <path d="M590 0 H700 V400 H38 C300 320 500 190 590 0 Z" fill="var(--brand-blue)"/>
      <path d="M470 0 C440 180 280 320 14 400 H0 V0 Z" fill="var(--card-white)"/>
    </svg>

    <div class="wordmark"><span class="wordmark-square"></span>Halden Group</div>

    <div class="holder">
      <p class="holder-name">Martin Ellery</p>
      <p class="holder-role">Owner</p>
    </div>

    <ul class="contact-list">
      <li class="contact-item">+0000-0000-0000
        <span class="contact-icon"><svg viewBox="0 0 24 24"><path d="M6.6 10.8a15.5 15.5 0 0 0 6.6 6.6l2.2-2.2c.3-.3.7-.4 1-.2 1.1.4 2.3.6 3.6.6.6 0 1 .4 1 1V20c0 .6-.4 1-1 1A17 17 0 0 1 3 4c0-.6.4-1 1-1h3.5c.6 0 1 .4 1 1 0 1.3.2 2.5.6 3.6.1.3 0 .7-.2 1z"/></svg></span>
      </li>
      <li class="contact-item">info@yourdomain.com
        <span class="contact-icon"><svg viewBox="0 0 24 24"><path d="M2 5h20v14H2z M4 7v.5l8 5 8-5V7l-8 5z" fill-rule="evenodd"/></svg></span>
      </li>
      <li class="contact-item">www.yourdomain.com
        <span class="contact-icon"><svg viewBox="0 0 24 24"><path d="M12 2a10 10 0 1 0 0 20 10 10 0 0 0 0-20zm0 3a7 7 0 1 1 0 14 7 7 0 0 1 0-14z" fill-rule="evenodd"/></svg></span>
      </li>
      <li class="contact-item">Suite 8, 22 Marlow Lane, Bristol
        <span class="contact-icon"><svg viewBox="0 0 24 24"><path d="M12 2a7 7 0 0 0-7 7c0 5 7 13 7 13s7-8 7-13a7 7 0 0 0-7-7zm0 4.5a2.5 2.5 0 1 1 0 5 2.5 2.5 0 0 1 0-5z" fill-rule="evenodd"/></svg></span>
      </li>
    </ul>
  </section>

</body>
</html>
```